Beauty Therapy Web Design

I need a web page design for a small beauty therapy clinic, the owner is currently the only beauty therapist working there.
We require the following pages:
Home
About
Treatments
Nails
Courses
Contact
I will attach the clinics business card, treatment menu and signage so that you get a feeling for the branding colours etc.
This is the first website for the beauty therapist, she would like to attract new clients and also tourists that come in on the cruise ships. The thing that sets her apart from other clinics is that she welcomes texting for appointments.
I have selected refundable because I have never done this before so I don't know what to expect, I have the full intention of going through with it as long as I get a good design.
Feel free to ask for further information
Reason: Project extended as I am away for work and am unable to meet with the owner.
Target Market(s)
Females 18 to 50
Industry/Entity Type
Business
Look and feel

```html
<!DOCTYPE html>
<html lang="en">
<head>
<meta charset="utf-8">
<title>Velora Beauty Therapy Treatments</title>
<link rel="stylesheet" href="https://fonts.googleapis.com/css2?family=Parisienne&family=Fredoka:wght@500&family=Fondamento&family=Tinos&display=swap">
<style>
  :root {
    --backdrop: #c43fcb;
    --backdrop-deep: #a92cb3;
    --page: #ffffff;
    --ink-grey: #9a9a9a;
    --ink-dark: #555555;
    --accent-purple: #a51fe0;
    --bar-purple: #c92ef0;
    --gold: #f2bd00;
    --frame-grey: #bcbcbc;
    --rule: #c8c8c8;
    --banner-red: #cc1111;
  }
  * { box-sizing: border-box; margin: 0; padding: 0; }
  html, body { width: 1200px; height: 900px; overflow: hidden; }
  body {
    position: relative;
    background: radial-gradient(circle at 50% 50%, var(--backdrop), var(--backdrop-deep));
    font-family: "Fredoka", sans-serif;
  }
  .page {
    position: absolute; left: 20px; top: 20px; width: 1160px; height: 860px;
    background: var(--page); border-radius: 12px;
    box-shadow: 0 0 6px rgba(0,0,0,.35);
  }
  .abs { position: absolute; }

  .brand-name {
    left: 84px; top: 68px; font-family: "Parisienne", cursive;
    font-size: 56px; line-height: 1; color: var(--gold);
  }
  .brand-mark { left: 60px; top: 40px; width: 22px; height: 22px; border-radius: 50%; background: var(--gold); }
  .tagline {
    left: 313px; top: 86px; font-family: "Parisienne", cursive;
    font-size: 28px; color: var(--ink-dark); line-height: 1;
  }
  .appointment { right: 80px; top: 72px; text-align: center; font-family: "Parisienne", cursive; color: var(--ink-dark); }
  .appointment .label { font-size: 20px; line-height: 1.1; }
  .appointment .phone { font-size: 26px; line-height: 1.1; color: #666; }

  .main-nav {
    left: 0; width: 1200px; top: 158px; text-align: center;
    font-size: 28px; color: var(--ink-grey); letter-spacing: .3px;
  }
  .main-nav a { color: inherit; text-decoration: none; }
  .main-nav a.current { color: var(--accent-purple); }
  .main-nav .sep { margin: 0 26px; }

  .rule { left: 140px; width: 915px; height: 1px; background: var(--rule); }
  .rule-ornament { width: 100px; height: 14px; left: 550px; border-radius: 7px; background: linear-gradient(90deg, transparent, #d6d6d6, transparent); }

  .slider-frame {
    left: 84px; top: 228px; width: 1036px; height: 255px;
    background: #f1f1f1; border: 1px solid #d9d9d9;
    box-shadow: 2px 3px 5px rgba(0,0,0,.3);
  }
  .slider-image {
    left: 101px; top: 246px; width: 1001px; height: 218px;
    border: 1.5px solid var(--banner-red);
    background: linear-gradient(90deg, #8c98a3 0%, #c9cdd0 25%, #c99a82 40%, #e2b9a1 58%, #e8cdbb 75%, #c6dbe6 88%, #f4f4f4 100%);
  }
  .slider-caption {
    left: 101px; top: 415px; width: 689px; height: 48px;
    background: rgba(20,20,20,.78); color: #fff;
    font-family: "Fondamento", cursive; font-size: 24px; letter-spacing: 1.5px;
    padding: 10px 0 0 18px;
  }
  .slider-arrow { top: 334px; }

  .headline {
    left: 0; width: 1200px; top: 512px; text-align: center;
    font-family: "Parisienne", cursive; font-size: 42px; color: var(--accent-purple);
  }

  .card { top: 575px; width: 322px; height: 217px; background: var(--frame-grey); border-radius: 8px 8px 0 0; box-shadow: 2px 2px 4px rgba(0,0,0,.25); }
  .card-image { position: absolute; left: 10px; top: 9px; width: 300px; height: 172px; }
  .card-bar {
    position: absolute; left: 0; bottom: 0; width: 322px; height: 36px;
    background: var(--bar-purple); display: flex; justify-content: space-between; align-items: center;
    padding: 0 10px 0 10px;
  }
  .card-title { font-family: "Parisienne", cursive; font-size: 28px; color: var(--gold); }
  .card-view { font-family: "Parisienne", cursive; font-size: 22px; color: #fff; }
  .service-list {
    position: absolute; left: 10px; top: 9px; width: 228px; height: 172px;
    background: #f3f3f3; list-style: none; padding: 6px 0 0 3px;
    font-family: "Tinos", serif; font-size: 13px; color: var(--accent-purple); line-height: 22.3px;
  }
  .service-photo { left: 238px; width: 72px; }

  .footer-nav { left: 82px; top: 831px; font-size: 15px; color: var(--ink-grey); }
  .footer-nav .sep { margin: 0 12px; }
  .copyright { right: 80px; top: 831px; font-size: 15px; color: var(--ink-grey); }
</style>
</head>
<body>
  <div class="page"></div>

  <header>
    <div class="abs brand-mark"></div>
    <div class="abs brand-name">Velora</div>
    <div class="abs tagline">Beauty Therapy Treatments</div>
    <div class="abs appointment">
      <div class="label">Text us for an Appointment</div>
      <div class="phone">027-555-0142</div>
    </div>
    <nav class="abs main-nav">
      <a class="current" href="#">Home</a><span class="sep">|</span><a href="#">Treatments</a><span class="sep">|</span><a href="#">About Us</a><span class="sep">|</span><a href="#">Nails</a><span class="sep">|</span><a href="#">Courses</a><span class="sep">|</span><a href="#">Contact Us</a>
    </nav>
  </header>

  <div class="abs rule" style="top:210px"></div>
  <div class="abs rule-ornament" style="top:203px" role="img" aria-label="Small scroll ornament"></div>

  <section>
    <div class="abs slider-frame"></div>
    <div class="abs slider-image" role="img" aria-label="Cruise ship beside a relaxed spa client"></div>
    <div class="abs slider-caption">Beautify Your Beauty With Your Beauty Expert .....</div>
    <svg class="abs slider-arrow" style="left:49px" width="36" height="36" viewBox="0 0 36 36">
      <circle cx="18" cy="18" r="17" fill="#d8d8d8" stroke="#aaa"/>
      <path d="M21 10 L13 18 L21 26" fill="none" stroke="#444" stroke-width="3.5" stroke-linecap="round" stroke-linejoin="round"/>
    </svg>
    <svg class="abs slider-arrow" style="left:1116px" width="36" height="36" viewBox="0 0 36 36">
      <circle cx="18" cy="18" r="17" fill="#d8d8d8" stroke="#aaa"/>
      <path d="M15 10 L23 18 L15 26" fill="none" stroke="#444" stroke-width="3.5" stroke-linecap="round" stroke-linejoin="round"/>
    </svg>
  </section>

  <div class="abs rule" style="top:504px"></div>
  <div class="abs rule-ornament" style="top:497px" role="img" aria-label="Small scroll ornament"></div>

  <h1 class="abs headline" style="font-weight:400">We also Treat tourists that come in on the cruise ships</h1>

  <section>
    <div class="abs card" style="left:98px">
      <div class="card-image" role="img" aria-label="Woman in a sun hat among spring blossoms" style="background:linear-gradient(135deg,#b9d89a 0%,#e6c9a8 45%,#d9a17e 70%,#f3eee6 100%)"></div>
      <div class="card-bar"><span class="card-title">Our Treatments</span><span class="card-view">View +</span></div>
    </div>
    <div class="abs card" style="left:438px">
      <ul class="service-list">
        <li>~ Facial</li><li>~ Waxing</li><li>~ Gail Nails</li><li>~ Manicures</li><li>~ Eye Lash</li><li>~ Eye Brow</li><li>~ Spray Tants</li>
      </ul>
      <div class="card-image service-photo" role="img" aria-label="Smiling woman in a green top" style="background:linear-gradient(180deg,#f1e3d8 0%,#e7c3a8 55%,#b7d88a 100%)"></div>
      <div class="card-bar"><span class="card-title">Our Services</span><span class="card-view">View +</span></div>
    </div>
    <div class="abs card" style="left:778px">
      <div class="card-image" role="img" aria-label="Glittering red gift boxes with a ribbon" style="background:linear-gradient(135deg,#c91f2e 0%,#e0475a 45%,#e89aa7 75%,#f2e1e4 100%)"></div>
      <div class="card-bar"><span class="card-title">Gift Vouchers</span><span class="card-view">View +</span></div>
    </div>
  </section>

  <div class="abs rule" style="top:810px"></div>
  <div class="abs rule-ornament" style="top:803px" role="img" aria-label="Small scroll ornament"></div>

  <footer>
    <nav class="abs footer-nav">
      <span>Home</span><span class="sep">|</span><span>Treatments</span><span class="sep">|</span><span>About Us</span><span class="sep">|</span><span>Nails</span><span class="sep">|</span><span>Courses</span><span class="sep">|</span><span>Contact Us</span>
    </nav>
    <div class="abs copyright">Copyright © Fernleaf Studio 2012</div>
  </footer>
</body>
</html>
```